Kelvaro.ch is looking for business card letterhead and envelope C5 with WOW effect

We need a strong business card for our company Kelvaro.ch, logo is available. You want a black or dark background on which the logo Stark r% 26 # 252; appears. Letterhead and envelope in C5 format should be in a similar design, but does not have to be We need a strong business card for our company Kelvaro.ch, logo is available. A black or dark background is desired, on which the logo Stark comes across. The letterhead and the envelope in C5 format should have a similar design.

Target Market(s)

Private customers as well as entrepreneurs

Contact Information for Business Card

E-mail: info@kelvaro-example.ch
Web.www.Kelvaro-example.ch
Tel: +41 ( 0 ) 79 482 6037
Adresse:
Lindenweg 14
9406 Tarnbach

Hier kann man Icons verwenden für Email,Tel und Adressse

Font styles to use
Other font styles liked:
• Dubai,bold

Colors

Designer to choose colors to be used in the design.

Requirements
Must have
• WOW effect
Nice to have
• R% 26 # 252; back business card with our service listings. - VEHICLE LABELING - SHOP WINDOW LABELING - STICKERS AND MUCH MORE ... in red color

```html
<!DOCTYPE html>
<html lang="en">
<head>
<meta charset="utf-8">
<title>Kelvaro.ch business card</title>
<link rel="stylesheet" href="https://fonts.googleapis.com/css2?family=Open+Sans:wght@400;600;700&family=Montserrat:wght@700;800&display=swap">
<style>
  :root {
    --stage: #4a4540;
    --card: #1b1b1c;
    --card-edge: #262627;
    --white: #f4f4f4;
    --muted: #d8d8d8;
    --yellow: #f7c928;
    --red: #d8121d;
    --hex-tone: #333335;
  }
  * { box-sizing: border-box; margin: 0; padding: 0; }
  html, body { width: 1200px; height: 930px; overflow: hidden; }
  body {
    background: var(--stage);
    font-family: "Open Sans", Arial, sans-serif;
    color: var(--white);
    position: relative;
  }
  .card {
    position: absolute;
    left: 300px;
    width: 600px;
    height: 388px;
    border-radius: 22px;
    background: linear-gradient(135deg, var(--card-edge) 0%, var(--card) 55%, #151515 100%);
    overflow: hidden;
  }
  .card--front { top: 57px; }
  .card--back  { top: 485px; }

  /* front */
  .brand-square {
    position: absolute;
    left: 110px; top: 118px;
    width: 120px; height: 120px;
    background: var(--yellow);
    border-radius: 4px;
  }
  .brand-name {
    position: absolute;
    font-family: "Open Sans", Arial, sans-serif;
    font-weight: 700;
    color: var(--white);
    letter-spacing: 1px;
  }
  .card--front .brand-name { left: 256px; top: 112px; font-size: 42px; }
  .services {
    position: absolute;
    right: 86px; top: 182px;
    list-style: none;
    text-align: right;
  }
  .services li {
    font-size: 15px;
    line-height: 22px;
    color: var(--white);
    text-transform: uppercase;
  }
  .services li::after {
    content: "";
    display: inline-block;
    width: 9px; height: 9px;
    margin-left: 10px;
    border: 2px solid var(--red);
    border-radius: 50%;
    vertical-align: 1px;
  }

  /* back */
  .pattern-area {
    position: absolute;
    left: 110px; top: 60px;
    width: 420px; height: 320px;
    background: radial-gradient(ellipse at 50% 55%, var(--hex-tone) 0%, rgba(51,51,53,0.5) 45%, rgba(27,27,28,0) 75%);
  }
  .card--back .brand-name { left: 0; right: 0; top: 72px; text-align: center; font-size: 30px; padding-left: 60px; }
  .person {
    position: absolute;
    right: 290px; top: 200px;
    text-align: right;
  }
  .person__name {
    font-family: "Montserrat", Arial, sans-serif;
    font-weight: 800;
    font-size: 28px;
    letter-spacing: 0.5px;
    text-transform: uppercase;
  }
  .person__name .accent { color: var(--yellow); }
  .person__role { font-size: 16px; color: var(--muted); margin-top: 4px; }
  .divider {
    position: absolute;
    left: 330px; top: 172px;
    width: 2px; height: 92px;
    background: var(--yellow);
  }
  .contact {
    position: absolute;
    left: 350px; top: 170px;
    list-style: none;
  }
  .contact li {
    display: flex; align-items: center;
    font-size: 15px; line-height: 31px;
    color: var(--white);
  }
  .contact svg { width: 15px; height: 15px; margin-right: 10px; flex: none; }
  .address {
    position: absolute;
    right: 60px; top: 308px;
    font-size: 16px;
    color: var(--white);
    letter-spacing: 0.3px;
  }
</style>
</head>
<body>

<section class="card card--front" aria-label="Business card front">
  <span class="brand-square" aria-hidden="true"></span>
  <div class="brand-name">KELVARO.CH</div>
  <ul class="services">
    <li>Vehicle labeling</li>
    <li>Shop window labeling</li>
    <li>Stickers and much more</li>
  </ul>
</section>

<section class="card card--back" aria-label="Business card back">
  <div class="pattern-area" role="img" aria-label="Faint dark honeycomb pattern decoration"></div>
  <div class="brand-name">KELVARO.CH</div>

  <div class="person">
    <div class="person__name">Lukas <span class="accent">Brenner</span></div>
    <div class="person__role">Director</div>
  </div>

  <span class="divider" aria-hidden="true"></span>

  <ul class="contact">
    <li>
      <svg viewBox="0 0 16 16" aria-hidden="true"><path fill="#f7c928" d="M3.6 1.2l2.3 2.6-1.3 1.8c.9 2 2.6 3.7 4.6 4.6l1.8-1.3 2.6 2.3-1.4 2.3C7.1 13.8 2.2 8.9 1.5 3.8z"/></svg>
      +41 ( 0 ) 79 482 6037
    </li>
    <li>
      <svg viewBox="0 0 16 16" aria-hidden="true"><rect x="1.5" y="3.5" width="13" height="9" fill="none" stroke="#f7c928" stroke-width="1.6"/><path d="M1.8 4l6.2 4.8L14.2 4" fill="none" stroke="#f7c928" stroke-width="1.6"/></svg>
      info@kelvaro-example.ch
    </li>
    <li>
      <svg viewBox="0 0 16 16" aria-hidden="true"><circle cx="8" cy="8" r="6.3" fill="none" stroke="#f7c928" stroke-width="1.5"/><ellipse cx="8" cy="8" rx="2.7" ry="6.3" fill="none" stroke="#f7c928" stroke-width="1.3"/><path d="M1.8 8h12.4M2.8 5h10.4M2.8 11h10.4" stroke="#f7c928" stroke-width="1.2"/></svg>
      www.Kelvaro-example.ch
    </li>
  </ul>

  <div class="address">Lindenweg 14 &nbsp;9406 Tarnbach</div>
</section>

</body>
</html>
```